1 Dimensional cover for digital product

Please note that if a designer comes in with an original design and other designers try to copy them too closely I will always work with the original designer in order to get the actual look I want.
Therefore it is in the interests of the designers to get their concepts in first.

I am designing some audio products for football (soccer players).

I would like a square version and a 16:9 version of the packaging completed. The square version will be for the Sonvia audio cover and the 16:9 for the thumbnails of videos.

I would like the final images in PSP files as a template that I can change the title and the main image.

I am open to creativity in this project but would like it to be a luxury and premium in what it is portraying.

I have added my logo and also the packaging that I currently use on my sister website which is not aimed at football, soccer.

I've also included an image of one of my models. This would NOT be the product image, but it could be a background image, or you may choose to leave it out altogether.

I've also included an example image as the main product image.

Although I have chosen greyscale I would also like to see products with colour.

The product page is at https://kelvarn.global/collections/all
I add this so that you can chose any one of the titles for this template

Target Market(s)

This is aimed at professional footballers

Industry/Entity Type

Sporting Good

Font styles to use
Serif
Sans Serif

Colors

Designer to choose colors to be used in the design.

Requirements
Must have
• This must look like it is made for an affluent market.
• It may also be simple in its design but I do not wish to be too prescriptive with creativity.
• My typography is Montserrat
Nice to have
• Can include the colors of my logos:
• #5BA9DE
• #272B5F
• Or you can choose to go with greyscale
Should not have
• This is a product for serious athletes so it should look very professional and adult orientated (so not cartoonish its look)

```html
<!DOCTYPE html>
<html lang="en">
<head>
<meta charset="utf-8">
<title>After Game – Hypnosis Sessions</title>
<link href="https://fonts.googleapis.com/css2?family=Montserrat:wght@300;400;600;800&display=swap" rel="stylesheet">
<style>
  :root {
    --sky: #5BA9DE;
    --navy: #272B5F;
    --amber: #E9A820;
    --amber-deep: #E2A02A;
    --sun: #F5D11E;
    --gold-text: #B6A45C;
    --paper: #FFFFFF;
    --photo-light: #B9B49A;
    --photo-dark: #2E2C25;
  }
  * { margin: 0; padding: 0; box-sizing: border-box; }
  html, body { width: 1200px; height: 675px; overflow: hidden; background: var(--paper); }
  .cover {
    position: relative;
    width: 1200px;
    height: 675px;
    overflow: hidden;
    background: var(--paper);
    font-family: "Montserrat", sans-serif;
  }
  .cover__shapes { position: absolute; inset: 0; }
  .brand {
    position: absolute;
    left: 56px;
    top: 64px;
    width: 186px;
    text-align: center;
    color: var(--paper);
  }
  .brand__dot {
    display: block;
    width: 30px;
    height: 30px;
    margin: 0 auto 10px;
    border-radius: 50%;
    background: var(--paper);
  }
  .brand__name {
    font-size: 9.5px;
    font-weight: 600;
    letter-spacing: 0.02em;
    white-space: nowrap;
  }
  .brand__tag {
    display: flex;
    align-items: center;
    gap: 6px;
    margin-top: 2px;
    font-size: 11px;
    font-weight: 600;
    letter-spacing: 0.08em;
  }
  .brand__tag::before, .brand__tag::after {
    content: "";
    flex: 1;
    height: 1px;
    background: var(--paper);
  }
  .title-block {
    position: absolute;
    right: 699px;
    top: 230px;
    text-align: right;
  }
  .title-block__kicker {
    font-size: 20px;
    font-weight: 600;
    color: var(--gold-text);
    margin-bottom: 14px;
  }
  .title-block__title {
    font-size: 128px;
    font-weight: 800;
    line-height: 0.78;
    color: var(--navy);
    letter-spacing: -0.01em;
  }
  .title-block__title span { display: block; margin-top: 10px; }
  .tagline {
    position: absolute;
    left: 160px;
    top: 561px;
    font-size: 13px;
    font-weight: 400;
    line-height: 1.35;
    text-transform: uppercase;
    color: var(--gold-text);
    letter-spacing: 0.01em;
  }
</style>
</head>
<body>
<main class="cover">
  <svg class="cover__shapes" width="1200" height="675" viewBox="0 0 1200 675" aria-hidden="false">
    <defs>
      <linearGradient id="photo-tone" x1="0" y1="0" x2="1" y2="1">
        <stop offset="0" stop-color="var(--photo-dark)"/>
        <stop offset="0.55" stop-color="#6E6A55"/>
        <stop offset="1" stop-color="var(--photo-light)"/>
      </linearGradient>
      <filter id="frame-shadow" x="-10%" y="-10%" width="120%" height="120%">
        <feDropShadow dx="0" dy="2" stdDeviation="6" flood-color="#000" flood-opacity="0.12"/>
      </filter>
    </defs>

    <polygon class="corner-band" points="0,0 373,0 0,373" fill="var(--sky)"/>

    <polygon class="accent accent--amber-left" points="628,250 860,390 628,556" fill="var(--amber)"/>
    <polygon class="accent accent--amber-top" points="986,172 1113,246 986,322" fill="var(--amber)"/>
    <polygon class="accent accent--amber-low" points="853,470 1030,420 1030,576" fill="var(--amber-deep)"/>
    <polygon class="accent accent--amber-base" points="770,520 1030,460 853,577" fill="var(--amber)"/>
    <polygon class="accent accent--sky-right" points="934,433 1124,268 1124,539" fill="var(--sky)"/>
    <polygon class="accent accent--sun-right" points="1124,339 1195,379 1124,418" fill="var(--sun)"/>
    <polygon class="accent accent--sun-low" points="770,535 853,577 770,624" fill="var(--sun)"/>

    <polygon class="photo-frame" points="662,51 1133,321 662,586" fill="var(--paper)" filter="url(#frame-shadow)"/>
    <polygon class="photo-frame__image" points="676,66 1114,321 676,570" fill="url(#photo-tone)"
             role="img" aria-label="Sepia photo of two footballers leaping for a ball under stadium lights"/>

    <polygon class="pointer pointer--navy" points="524,316 605,269 605,363" fill="var(--navy)"/>
    <polygon class="pointer pointer--amber" points="98,540 146,568 98,596" fill="var(--amber)"/>
  </svg>

  <div class="brand">
    <span class="brand__dot"></span>
    <div class="brand__name">KELVARN HYPNOTHERAPY</div>
    <div class="brand__tag">PEAK STATE</div>
  </div>

  <div class="title-block">
    <p class="title-block__kicker">Hypnosis sessions</p>
    <h1 class="title-block__title">AFTER<span>GAME</span></h1>
  </div>

  <p class="tagline">Conditioning you towards<br>even better future performances.</p>
</main>
</body>
</html>
```